Business Cards - Brightpath Horizon

need to design unique business card for my mortgage business. I need to design credit card style business card for my business or any unique idea that you might have

Target Market(s)

Home Loan customers

Industry/Entity Type

Mortgage Brokerage

Contact Information for Business Card

please design credit card style or very unique style business card

Colors

Designer to choose colors to be used in the design.

Requirements
Must have
• Name
• position
• Phone number
• fax number
• email address
• website address
• social media address
• All above fields will be provided once design in finalised

```html
<!DOCTYPE html>
<html lang="en">
<head>
<meta charset="utf-8">
<title>Brightpath Horizon – Business Card</title>
<link href="https://fonts.googleapis.com/css2?family=Work+Sans:wght@400;500&display=swap" rel="stylesheet">
<style>
  :root{
    --backdrop:#1b1b1d;
    --card-white:#ffffff;
    --navy:#314ca0;
    --sky:#1ea5e0;
    --orange:#f28c1c;
    --ink:#3a3a3a;
  }
  *{margin:0;padding:0;box-sizing:border-box}
  html,body{width:1200px;height:897px;overflow:hidden;background:var(--backdrop)}
  body{position:relative;font-family:"Work Sans",sans-serif}
  .card{position:absolute;left:303px;width:595px;height:339px;border-radius:21px;overflow:hidden}
  .card--front{top:92px;background:var(--card-white)}
  .card--back{top:469px;background:var(--navy)}

  .brand{position:absolute;display:flex;align-items:center;gap:10px;font-weight:500;letter-spacing:.5px}
  .brand__dot{width:14px;height:14px;border-radius:50%;flex:none}
  .card--front .brand{right:27px;top:64px;font-size:26px;color:var(--navy)}
  .card--front .brand__dot{background:var(--orange)}
  .card--back .brand{left:0;right:0;top:148px;justify-content:center;font-size:34px;color:#fff}
  .card--back .brand__dot{background:var(--orange);width:18px;height:18px}

  .person{position:absolute;left:24px;top:161px}
  .person__name{font-size:21px;font-weight:500;color:var(--sky);letter-spacing:1.6px;text-transform:uppercase}
  .person__role{font-size:14px;color:var(--ink);margin-top:6px;letter-spacing:.4px}

  .divider{position:absolute;left:24px;width:544px;top:228px;height:1.5px;background:var(--orange)}

  .contacts{position:absolute;left:24px;top:241px;list-style:none;font-size:14px;color:var(--ink);line-height:17.5px}
  .contacts li{display:flex;align-items:center;gap:8px}
  .contacts svg{width:9px;height:9px;flex:none}

  .address{position:absolute;right:27px;top:258px;text-align:right;font-size:14px;color:var(--ink);line-height:17.5px}

  .wave{position:absolute;left:0;bottom:0;width:595px;height:30px}

  .back__url{position:absolute;left:0;right:0;top:296px;text-align:center;color:#fff;font-size:13.5px;letter-spacing:1.6px}
</style>
</head>
<body>
  <section class="card card--front">
    <div class="brand"><span class="brand__dot"></span>Brightpath Horizon</div>

    <div class="person">
      <h1 class="person__name">Daniel Carter</h1>
      <p class="person__role">Founder</p>
    </div>

    <div class="divider"></div>

    <ul class="contacts">
      <li><svg viewBox="0 0 10 10"><path d="M2 1l2 2-1 1.2c.6 1.3 1.5 2.2 2.8 2.8L7 6l2 2-1.3 1.3C4.5 9 1 5.5.7 2.3z" fill="var(--sky)"/></svg>555-014-2273</li>
      <li><svg viewBox="0 0 10 10"><rect x=".7" y="2" width="8.6" height="6" fill="none" stroke="var(--sky)" stroke-width="1.2"/><path d="M.7 2L5 5.5 9.3 2" fill="none" stroke="var(--sky)" stroke-width="1.2"/></svg>hello@brightpathmail.com</li>
      <li><svg viewBox="0 0 10 10"><circle cx="5" cy="5" r="4.2" fill="none" stroke="var(--sky)" stroke-width="1.1"/><path d="M.8 5h8.4M5 .8c-2.2 2.5-2.2 5.9 0 8.4M5 .8c2.2 2.5 2.2 5.9 0 8.4" fill="none" stroke="var(--sky)" stroke-width=".9"/></svg>www.BrightpathHorizon.com</li>
    </ul>

    <address class="address" style="font-style:normal">480 Linden Grove Ave.<br>Fairhaven, FL 33012</address>

    <svg class="wave" viewBox="0 0 595 30" preserveAspectRatio="none">
      <path d="M0 5H345C358 5 362 10 352 10H0z" fill="var(--sky)"/>
      <path d="M0 18H335C365 18 380 2 420 0H595V30H0z" fill="var(--navy)"/>
    </svg>
  </section>

  <section class="card card--back">
    <div class="brand"><span class="brand__dot"></span>Brightpath Horizon</div>
    <p class="back__url">www.yourwebsite.com</p>
  </section>
</body>
</html>
```